Corvane Freight Company Business Card Design

We are a company that delivers natural saltwater (from the ocean) to aquarium companies, restaurants and home marine tanks. I would like a new business card to suit.

Must include Name, company name, abn, contact number and website as well as logo (see attached).

Looking for a design that stands out, has a clean but unique appearance.

Double and single sided entries welcome

Business

• Logo

```html
<!DOCTYPE html>
<html lang="en">
<head>
<meta charset="utf-8">
<title>Corvane Freight Company Business Card</title>
<link href="https://fonts.googleapis.com/css2?family=Open+Sans:wght@400;700&family=Questrial&display=swap" rel="stylesheet">
<style>
  :root {
    --backdrop: #2b2b2d;
    --ocean: #1f6fe8;
    --ocean-deep: #1a5fd6;
    --lagoon: #6ee8fb;
    --lagoon-light: #b9f6ff;
    --sky-text: #3fb2f0;
    --white: #ffffff;
    --ink: #0b0b0b;
  }
  html, body {
    margin: 0;
    padding: 0;
    width: 1200px;
    height: 1102px;
    overflow: hidden;
    background: var(--backdrop);
  }
  .stage { position: relative; width: 1200px; height: 1102px; }
  .card {
    position: absolute;
    width: 793px;
    height: 452px;
    border-radius: 22px;
    overflow: hidden;
  }
  .card-front { left: 76px; top: 71px; background: var(--ocean); }
  .card-back {
    left: 334px; top: 568px;
    background: radial-gradient(ellipse at 50% 48%, var(--lagoon-light) 0%, var(--lagoon) 70%);
  }
  .wave-band { position: absolute; left: 0; top: 0; width: 793px; height: 452px; }
  .brand {
    position: absolute;
    display: flex;
    align-items: center;
    gap: 14px;
    font-family: "Open Sans", sans-serif;
    font-weight: 700;
    font-size: 50px;
    white-space: nowrap;
    transform: translate(-50%, -50%);
  }
  .brand-dot { width: 26px; height: 26px; border-radius: 50%; }
  .card-front .brand { left: 395px; top: 118px; color: var(--white); }
  .card-front .brand-dot { background: var(--lagoon); }
  .card-back .brand { left: 396px; top: 210px; color: var(--ocean-deep); }
  .card-back .brand-dot { background: var(--ocean-deep); }
  .company-address {
    position: absolute;
    right: 401px;
    top: 237px;
    text-align: right;
    font-family: "Questrial", sans-serif;
    font-size: 19px;
    line-height: 27px;
    color: var(--white);
  }
  .company-address .company-name { font-size: 21px; }
  .divider {
    position: absolute; left: 415px; top: 239px;
    width: 1px; height: 86px; background: var(--white);
  }
  .contact {
    position: absolute; left: 432px; top: 237px;
    font-family: "Questrial", sans-serif;
    font-size: 20px; line-height: 28px;
    color: var(--white); letter-spacing: 0.5px;
  }
  .contact-row { display: flex; align-items: center; gap: 8px; }
  .contact svg { width: 15px; height: 15px; }
  .holder {
    position: absolute; left: 637px; top: 372px;
    transform: translateX(-50%);
    text-align: center; color: var(--ink);
    font-family: "Open Sans", sans-serif;
  }
  .holder-name { font-weight: 700; font-size: 26px; line-height: 32px; }
  .holder-title { font-size: 21px; line-height: 28px; }
  .back-site {
    position: absolute; left: 0; right: 0; top: 362px;
    text-align: center;
    font-family: "Questrial", sans-serif;
    font-size: 23px; letter-spacing: 5px;
    color: var(--white);
  }
</style>
</head>
<body>
<main class="stage">
  <section class="card card-front" aria-label="Business card front">
    <svg class="wave-band" viewBox="0 0 793 452" aria-hidden="true">
      <path d="M0 380 C200 385 420 380 560 340 C660 312 740 300 793 296 L793 452 L0 452 Z" fill="#6ee8fb"/>
      <path d="M0 372 C200 378 420 372 560 332 C660 304 740 292 793 288" fill="none" stroke="#ffffff" stroke-width="6"/>
      <path d="M0 398 C160 410 330 412 470 385 C580 362 680 330 793 318 L793 340 C680 350 580 378 470 400 C330 428 160 424 0 414 Z" fill="#2f8df0" opacity="0.85"/>
      <path d="M0 418 C150 430 300 430 420 412" fill="none" stroke="#ffffff" stroke-width="2" opacity="0.8"/>
    </svg>

    <div class="brand"><span class="brand-dot"></span>Corvane Freight</div>

    <div class="company-address">
      <div class="company-name">Corvane Freight LLC</div>
      <div>Street Name, City Name</div>
      <div>State, City Zip Code</div>
    </div>
    <div class="divider"></div>
    <div class="contact">
      <div class="contact-row">
        <svg viewBox="0 0 16 16" aria-hidden="true"><circle cx="8" cy="8" r="7" fill="none" stroke="#fff" stroke-width="1.5"/><path d="M5 4.5 L6.6 4.5 L7.2 6.4 L6.2 7.2 C6.8 8.4 7.6 9.2 8.8 9.8 L9.6 8.8 L11.5 9.4 L11.5 11 C8 11.2 4.8 8 5 4.5 Z" fill="#fff"/></svg>
        <span>123-456-7890</span>
      </div>
      <div class="contact-row">
        <svg viewBox="0 0 16 16" aria-hidden="true"><circle cx="8" cy="8" r="7" fill="#fff"/><path d="M1 8 H15 M8 1 C5 4 5 12 8 15 M8 1 C11 4 11 12 8 15" fill="none" stroke="#1f6fe8" stroke-width="1"/></svg>
        <span>www.website.com</span>
      </div>
      <div class="contact-row"><span>ABN : 0123456789</span></div>
    </div>

    <div class="holder">
      <div class="holder-name">Your name</div>
      <div class="holder-title">Title</div>
    </div>
  </section>

  <section class="card card-back" aria-label="Business card back">
    <div class="brand"><span class="brand-dot"></span>Corvane Freight</div>
    <div class="back-site">www.website.com</div>
  </section>
</main>
</body>
</html>
```